Cover page and letterhead for athlete development program

We require an exciting and dynamic cover page with a second page letterhead in a word doc format for us to use as professional stationery for letter merges and portfolio documents. We are an athlete preparation company that specialises in training up and coming sports representatives in the fitness and sports science industry. We work with athletes from ages 13 - 24 mainly. If we could have images on the cover page from the sports of:
Rugby League
Rugby Union
Hockey
Cricket
AFL
Soccer
Track and Field
Netball
Basketball
Golf
Weight training

This would be a great start. Thank you

```html
<!DOCTYPE html>
<html lang="en">
<head>
<meta charset="utf-8">
<title>Rising Contender – Letterhead</title>
<link href="https://fonts.googleapis.com/css2?family=Arimo:wght@400;700&family=Montserrat:wght@800&display=swap" rel="stylesheet">
<style>
  :root {
    --backdrop: #d9dcde;
    --paper: #ffffff;
    --ink: #141414;
    --body-text: #7a7a7a;
    --gold: #d99a2b;
    --steel: #cfd0d2;
    --rule: #9a9a9a;
  }
  * { box-sizing: border-box; margin: 0; padding: 0; }
  html, body { width: 1200px; height: 784px; overflow: hidden; }
  body {
    background: var(--backdrop);
    font-family: "Arimo", Arial, sans-serif;
    display: flex; align-items: center; justify-content: center;
  }
  .letterhead {
    position: relative;
    width: 540px; height: 740px;
    background: var(--paper);
    box-shadow: 0 6px 18px rgba(0,0,0,.18);
    overflow: hidden;
  }
  .corner-art {
    position: absolute; width: 130px; height: 70px;
    background: linear-gradient(135deg, var(--gold) 0%, var(--steel) 100%);
    clip-path: polygon(0 0, 100% 0, 0 100%);
  }
  .corner-art--top { top: 0; left: 0; }
  .corner-art--bottom { bottom: 0; right: 0; transform: rotate(180deg); }

  .side-bar {
    position: absolute; left: 26px; top: 120px; bottom: 150px; width: 7px;
    background: linear-gradient(90deg, #000 0%, #3a3a3a 60%, #bbb 100%);
  }

  .brand {
    position: absolute; top: 44px; right: 40px;
    display: flex; align-items: center; gap: 10px;
  }
  .brand__mark { width: 30px; height: 30px; background: var(--ink); }
  .brand__name {
    font-family: "Montserrat", Arial, sans-serif; font-weight: 800;
    font-size: 21px; line-height: 1.05; letter-spacing: .5px;
    color: var(--ink); text-transform: uppercase;
  }

  .letter-body {
    position: absolute; top: 140px; left: 118px; width: 380px;
    font-size: 10.5px; line-height: 1.5; color: var(--body-text);
  }
  .letter-body p { margin-bottom: 12px; }

  .signature {
    position: absolute; top: 590px; left: 150px; width: 180px; height: 40px;
    background: linear-gradient(90deg, rgba(150,150,150,.14), rgba(150,150,150,.05));
    border-radius: 4px;
  }

  .contact {
    position: absolute; left: 58px; bottom: 44px; width: 360px;
    color: var(--ink);
  }
  .contact__icons { display: flex; align-items: center; gap: 6px; margin-bottom: 8px; }
  .contact__icons .rule { flex: 1; height: 1px; background: var(--rule); }
  .contact__icons svg { width: 12px; height: 12px; }
  .contact__address { font-weight: 700; font-size: 10px; margin-bottom: 4px; }
  .contact__lines { font-size: 8.5px; color: #555; }
  .contact__lines span + span::before { content: "|"; margin: 0 6px; color: #999; }
</style>
</head>
<body>
  <main class="letterhead">
    <div class="corner-art corner-art--top" role="img" aria-label="Decorative folded corner in gold, grey and black"></div>

    <div class="side-bar"></div>

    <header class="brand">
      <span class="brand__mark"></span>
      <span class="brand__name">Rising<br>Contender</span>
    </header>

    <section class="letter-body">
      <p>Lorem Ipsum is simply dummy text of the printing and typesetting industry. Lorem Ipsum has been the industry's standard dummy text ever since the 1500s, when an unknown printer took a galley of type and scrambled it to make a type specimen book. It has survived not only five centuries, but also the leap into electronic typesetting, remaining essentially unchanged. It was popularised in the 1960s with the release of Typeline sheets containing Lorem Ipsum passages, and more recently with desktop publishing software like PageCraft Studio including versions of Lorem Ipsum.</p>
      <p>It is a long established fact that a reader will be distracted by the readable content of a page when looking at its layout. The point of using Lorem Ipsum is that it has a more-or-less normal distribution of letters, as opposed to using 'Content here, content here', making it look like readable English. Many desktop publishing packages and web page editors now use Lorem Ipsum as their default model text, and a search for 'lorem ipsum' will uncover many web sites still in their infancy. Various versions have evolved over the years, sometimes by accident, sometimes on purpose (injected humour and the like).</p>
      <p>Contrary to popular belief, Lorem Ipsum is not simply random text. It has roots in a piece of classical Latin literature from 45 BC, making it over 2000 years old. Martin Ellsworth, a Latin professor at Harlow Ridge College, looked up one of the more obscure Latin words, consectetur, from a Lorem Ipsum passage, and going through the cites of the word in classical literature, discovered the undoubtable source. Lorem Ipsum comes from sections 1.10.32 and 1.10.33 of "de Finibus Bonorum et Malorum" structures, to generate Lorem Ipsum which looks reasonable. The generated Lorem Ipsum is therefore always free from repetition, injected humour, or non-characteristic words etc.</p>
    </section>

    <div class="signature" role="img" aria-label="Handwritten signature of the sender"></div>

    <footer class="contact">
      <div class="contact__icons">
        <span class="rule"></span>
        <svg viewBox="0 0 12 12" aria-label="Location"><circle cx="6" cy="6" r="6" fill="var(--ink)"/><path d="M6 2.5a2 2 0 0 1 2 2c0 1.5-2 4-2 4s-2-2.5-2-4a2 2 0 0 1 2-2z" fill="#fff"/></svg>
        <svg viewBox="0 0 12 12" aria-label="Phone"><circle cx="6" cy="6" r="6" fill="var(--ink)"/><path d="M4 3l1.2 1.3-.6.8a4 4 0 0 0 2.3 2.3l.8-.6L9 8l-.8 1C6 9 3 6 3 3.8z" fill="#fff"/></svg>
        <svg viewBox="0 0 12 12" aria-label="Email"><circle cx="6" cy="6" r="6" fill="var(--ink)"/><rect x="3" y="4" width="6" height="4" fill="#fff"/><path d="M3 4l3 2.2L9 4" stroke="var(--ink)" stroke-width=".7" fill="none"/></svg>
        <svg viewBox="0 0 12 12" aria-label="Website"><circle cx="6" cy="6" r="6" fill="var(--ink)"/><circle cx="6" cy="6" r="3" fill="none" stroke="#fff" stroke-width=".8"/><path d="M3 6h6M6 3v6" stroke="#fff" stroke-width=".6"/></svg>
        <svg viewBox="0 0 12 12" aria-label="Contact"><circle cx="6" cy="6" r="6" fill="var(--ink)"/><circle cx="6" cy="6" r="2.6" fill="#fff"/></svg>
        <span class="rule"></span>
      </div>
      <p class="contact__address">Level 3, 48 Harbourline Parade, Fremantle, Western Australia 6160</p>
      <p class="contact__lines"><span>000.0000.000</span><span>000.0000.000</span><span>info@risingcontender.com.au</span><span>www.risingcontender.com.au</span></p>
    </footer>

    <div class="corner-art corner-art--bottom" role="img" aria-label="Decorative folded corner in gold, grey and black"></div>
  </main>
</body>
</html>
```